Oil Field Service company needs professional business cards

Looking to clean up our current company business cards and look a little more professional. Brenwick Casing Services is a US based company that services the oil field. We deal with engineers, managers and oil rigs....................................................................................................................................................................................................................................................................................................................................................................................................

Target Market(s)

Oil and Gas professionals

Industry/Entity Type

Oil And Gas

Contact Information for Business Card

See attached photo as example

Font styles to use
Sans Serif

Colors
ec1f27

Requirements
Must have
• Company Logo, Name, Title, Cell, Office, Fax, Email.
• See attached photo
Nice to have
• External CRT, Internal CRT, Casing Crews, Torque Turn, Laydown Machine
Should not have
• Do not introduce any new pictures and keep it professional looking

```html
<!DOCTYPE html>
<html lang="en">
<head>
<meta charset="utf-8">
<title>Brenwick Casing Services – Business Card</title>
<link href="https://fonts.googleapis.com/css2?family=Open+Sans:wght@400;600;700&display=swap" rel="stylesheet">
<style>
  :root {
    --backdrop: #4b4d50;
    --slate: #45535e;
    --brand-red: #ec1f27;
    --ink: #45535e;
    --text-grey: #4a4a4a;
    --rule: #8a8f94;
    --paper: #ffffff;
  }
  * { margin: 0; padding: 0; box-sizing: border-box; }
  html, body {
    width: 1105px; height: 1200px; overflow: hidden;
    background: var(--backdrop);
    font-family: "Open Sans", Arial, sans-serif;
  }
  .card {
    position: absolute; left: 196px;
    width: 720px; height: 413px;
  }
  .card--front { top: 145px; background: var(--paper); }
  .card--back { top: 602px; background: var(--slate); color: var(--paper); }

  .side-band {
    position: absolute; left: 0; top: 0; bottom: 0; width: 36px;
    background: var(--slate);
  }
  .side-line {
    position: absolute; left: 38px; top: 0; bottom: 0; width: 3px;
    background: var(--brand-red);
  }

  .wordmark {
    position: absolute; text-align: center;
    font-weight: 700; line-height: 1;
  }
  .wordmark__name { display: block; letter-spacing: 1px; }
  .wordmark__sub { display: block; letter-spacing: 3px; }
  .card--front .wordmark { right: 30px; top: 62px; width: 300px; color: var(--ink); }
  .card--front .wordmark__name { font-size: 50px; }
  .card--front .wordmark__sub { font-size: 17px; margin-top: 10px; }

  .holder { position: absolute; left: 66px; top: 196px; }
  .holder__name { color: var(--brand-red); font-size: 26px; font-weight: 600; line-height: 1.2; }
  .holder__title { color: var(--ink); font-size: 20px; line-height: 1.3; }

  .divider {
    position: absolute; left: 66px; right: 31px; top: 262px;
    height: 1px; background: var(--rule);
  }

  .contacts { position: absolute; left: 66px; top: 271px; list-style: none; }
  .contacts li {
    display: flex; align-items: center; height: 27.5px;
    font-size: 18.5px; color: var(--text-grey);
  }
  .contacts svg { width: 17px; height: 17px; margin: 0 14px 0 8px; fill: var(--brand-red); }

  .location {
    position: absolute; right: 25px; top: 325px; text-align: right;
    font-size: 18.5px; color: var(--text-grey); line-height: 27.5px;
  }

  .card--back .wordmark { left: 0; right: 0; top: 155px; }
  .card--back .wordmark__name { font-size: 62px; }
  .card--back .wordmark__sub { font-size: 21px; margin-top: 14px; letter-spacing: 4px; }

  .services {
    position: absolute; left: 0; right: 0; top: 318px;
    text-align: center; font-size: 19px; line-height: 27px;
  }
</style>
</head>
<body>

<section class="card card--front" aria-label="Business card front">
  <div class="side-band"></div>
  <div class="side-line"></div>

  <div class="wordmark">
    <span class="wordmark__name">BRENWICK</span>
    <span class="wordmark__sub">CASING SERVICES</span>
  </div>

  <div class="holder">
    <p class="holder__name">Cody Hallbrook</p>
    <p class="holder__title">Area Manager</p>
  </div>

  <div class="divider"></div>

  <ul class="contacts">
    <li>
      <svg viewBox="0 0 24 24" aria-label="Office"><path d="M6.6 10.8a15.1 15.1 0 0 0 6.6 6.6l2.2-2.2c.3-.3.7-.4 1-.2 1.1.4 2.3.6 3.6.6.6 0 1 .4 1 1V20c0 .6-.4 1-1 1C10.6 21 3 13.4 3 4c0-.6.4-1 1-1h3.5c.6 0 1 .4 1 1 0 1.3.2 2.5.6 3.6.1.3 0 .7-.2 1z"/></svg>
      (555)201-4800
    </li>
    <li>
      <svg viewBox="0 0 24 24" aria-label="Cell"><path d="M7 1h10a2 2 0 0 1 2 2v18a2 2 0 0 1-2 2H7a2 2 0 0 1-2-2V3a2 2 0 0 1 2-2zm0 3v14h10V4zm5 15.5a1.2 1.2 0 1 0 0 2.4 1.2 1.2 0 0 0 0-2.4z"/></svg>
      (555)318-6275
    </li>
    <li>
      <svg viewBox="0 0 24 24" aria-label="Fax"><path d="M6 2h12v6H6zM3 9h18a2 2 0 0 1 2 2v7h-4v4H5v-4H1v-7a2 2 0 0 1 2-2zm4 8v3h10v-3z"/></svg>
      (555)201-4839
    </li>
    <li>
      <svg viewBox="0 0 24 24" aria-label="Email"><path d="M2 5h20v14H2zm2 2v.5l8 5 8-5V7l-8 5z"/></svg>
      cody@brenwick.com
    </li>
  </ul>

  <div class="location">
    <p>Alderton, OK 73000</p>
    <p>www.brenwick.com</p>
  </div>
</section>

<section class="card card--back" aria-label="Business card back">
  <div class="wordmark">
    <span class="wordmark__name">BRENWICK</span>
    <span class="wordmark__sub">CASING SERVICES</span>
  </div>
  <div class="services">
    <p>External CRT • Internal CRT • Casing Crews</p>
    <p>Torque Turn • Laydown Machine</p>
  </div>
</section>

</body>
</html>
```